Healthcare and Professional IT Services Company need a redesigned business card

We are a IT Services company that targets small medical practices and professional business such as Attorneys, Accounts, Architects etc. We want to communicate a professional yet friendly image using recent logo redesign here on ArtHarbor. Like to see the colors blue and orange in the design. Must use the Tall Pine Computing as displayed in the new logo - then also want to incorporate the fish logo as well.

Target Market(s)

Small medical and professional services

Industry/Entity Type

It Company

Contact Information for Business Card

The usual stuff, place for name address phone website. Also maybe our tagline which is "rooted in technology"

Requirements
Must have
• My new logo and the fish somewhere on the card

```html
<!DOCTYPE html>
<html lang="en">
<head>
<meta charset="utf-8">
<title>Tall Pine Computing – Business Card</title>
<link rel="stylesheet" href="https://fonts.googleapis.com/css2?family=Open+Sans:ital,wght@0,400;0,600;0,700;1,700&display=swap">
<style>
  :root {
    --stage: #000000;
    --card: #ffffff;
    --brand-blue: #1a73c8;
    --brand-sky: #29a3e0;
    --brand-teal: #1596b8;
    --brand-orange: #f08a3c;
    --ink: #1c1c1c;
    --divider: #d9d9d9;
  }
  * { margin: 0; padding: 0; box-sizing: border-box; }
  html, body {
    width: 1200px; height: 900px; overflow: hidden;
    background: var(--stage);
    font-family: "Open Sans", Arial, sans-serif;
    color: var(--ink);
  }
  .card {
    position: absolute; top: 275px;
    width: 477px; height: 293px;
    background: var(--card);
  }
  .card--front { left: 116px; border-radius: 0 60px 0 60px; }
  .card--back  { left: 622px; border-radius: 60px 0 60px 0; }

  .brand {
    position: absolute; left: 30px; top: 88px; width: 205px;
    display: flex; align-items: center; gap: 10px;
  }
  .brand__dot {
    width: 18px; height: 18px; border-radius: 50%;
    background: var(--brand-orange); flex: none;
  }
  .brand__name {
    font-size: 24px; font-weight: 600; line-height: 1.15;
    color: var(--brand-sky);
  }

  .divider {
    position: absolute; left: 245px; top: 93px;
    width: 1px; height: 152px; background: var(--divider);
  }

  .contact {
    position: absolute; right: 22px; top: 32px;
    text-align: right;
  }
  .contact__name { font-size: 17px; font-weight: 700; color: var(--brand-blue); line-height: 22px; }
  .contact__role { font-size: 13px; line-height: 18px; }
  .contact__address { margin-top: 86px; font-size: 13px; line-height: 17px; }
  .contact__lines { margin-top: 23px; list-style: none; font-size: 13px; line-height: 17.5px; }
  .contact__lines li { display: flex; justify-content: flex-end; align-items: center; gap: 5px; }
  .contact__lines svg { width: 10px; height: 10px; fill: var(--brand-blue); flex: none; }

  .mascot {
    position: absolute; left: 128px; top: 70px;
    width: 225px; height: 152px; border-radius: 45% 50% 45% 50%;
    background: linear-gradient(100deg, var(--brand-orange) 0%, #5bb7e8 45%, #2f8fd0 75%, #e9e4f0 100%);
  }
  .tagline {
    position: absolute; left: 0; right: 0; top: 238px;
    text-align: center; font-size: 14px; font-weight: 700; font-style: italic;
    color: var(--brand-teal);
  }
  .tagline__accent { color: var(--brand-blue); }
</style>
</head>
<body>
  <section class="card card--front">
    <div class="brand">
      <span class="brand__dot"></span>
      <span class="brand__name">Tall Pine Computing</span>
    </div>
    <div class="divider"></div>
    <div class="contact">
      <p class="contact__name">Daniel Reyes</p>
      <p class="contact__role">Managing Director</p>
      <p class="contact__address">12345, Address Goes Here<br>Country Name, 123456.</p>
      <ul class="contact__lines">
        <li>044-123 456 789
          <svg viewBox="0 0 10 10"><path d="M2 0.5l2 2-1 1.2c.6 1.3 1.6 2.3 2.9 2.9l1.2-1 2 2-1.2 1.6C4.5 9.2.8 5.5.4 1.7z"/></svg>
        </li>
        <li>info@webname.com
          <svg viewBox="0 0 10 10"><path d="M0 2h10v6H0z M0.6 2.4L5 5.6l4.4-3.2" fill="var(--brand-blue)" stroke="#fff" stroke-width="0.8"/></svg>
        </li>
        <li>www.websitename.com
          <svg viewBox="0 0 10 10"><path d="M4 6l2-2M3.5 4.5L2 6a1.4 1.4 0 002 2l1.5-1.5M6.5 5.5L8 4a1.4 1.4 0 00-2-2L4.5 3.5" fill="none" stroke="var(--brand-blue)" stroke-width="1.2" stroke-linecap="round"/></svg>
        </li>
      </ul>
    </div>
  </section>

  <section class="card card--back">
    <div class="mascot" role="img" aria-label="Cartoon mascot illustration in blue and orange"></div>
    <p class="tagline">"<span class="tagline__accent">rooted</span> in technology"</p>
  </section>
</body>
</html>
```